Business Card Design

Please use the Logo for colors and styles, and create a business card using the following info:

Lukas Brenner
Web Developer

Talvo Systems
+41 78 412 65 08
lukas@talvo-systems.ch
www.talvo-systems.ch

Download the logo at http://talvo-systems.ch/tl_files/talvo_systems.zip

Thanks for your works!

```html
<!DOCTYPE html>
<html lang="en">
<head>
<meta charset="utf-8">
<title>Talvo Systems – Business Card</title>
<link rel="stylesheet" href="https://fonts.googleapis.com/css2?family=Jost:wght@400;500&display=swap">
<style>
  :root {
    --backdrop: #d9dadc;
    --card-blue: #0b6cb2;
    --card-blue-deep: #075a98;
    --card-white: #f7f8f9;
    --brand-blue: #1269ad;
    --text-dark: #3b3d40;
    --text-muted: #6b6e72;
    --white: #ffffff;
  }
  * { margin: 0; padding: 0; box-sizing: border-box; }
  html, body { width: 1200px; height: 900px; overflow: hidden; }
  body {
    background: var(--backdrop);
    font-family: "Jost", "Futura", sans-serif;
    position: relative;
  }
  .card {
    position: absolute;
    width: 580px;
    height: 331px;
    border-radius: 3px;
    overflow: hidden;
  }
  .card-back {
    left: 110px;
    top: 90px;
    background: linear-gradient(135deg, var(--card-blue-deep) 0%, var(--card-blue) 60%, #1a7bc1 100%);
  }
  .card-back .wordmark {
    position: absolute;
    left: 44px;
    top: 50%;
    transform: translate(-50%, -50%) rotate(-90deg);
    transform-origin: center;
    margin-left: 0;
    white-space: nowrap;
    color: var(--white);
    font-size: 26px;
    font-weight: 500;
    letter-spacing: 0.5px;
  }
  .card-back .wordmark-wrap {
    position: absolute;
    left: 44px;
    top: 0;
    bottom: 0;
    width: 0;
  }
  .card-front {
    left: 510px;
    top: 470px;
    background: var(--card-white);
  }
  .card-front .wordmark {
    position: absolute;
    left: 48px;
    top: 96px;
    color: var(--brand-blue);
    font-size: 34px;
    font-weight: 500;
    letter-spacing: 0.5px;
  }
  .contact {
    position: absolute;
    left: 50px;
    top: 206px;
  }
  .contact .person {
    display: flex;
    align-items: baseline;
    margin-bottom: 12px;
  }
  .contact .name {
    color: var(--brand-blue);
    font-size: 21px;
    font-weight: 500;
  }
  .contact .role {
    color: var(--text-muted);
    font-size: 12px;
    margin-left: 6px;
    padding-left: 5px;
    border-left: 1px solid var(--text-muted);
  }
  .contact .line {
    color: var(--text-dark);
    font-size: 13px;
    line-height: 17px;
  }
  .contact .company { font-size: 14px; }
</style>
</head>
<body>
  <section class="card card-back" aria-label="Business card, back">
    <div class="wordmark-wrap">
      <span class="wordmark">TALVO SYSTEMS</span>
    </div>
  </section>

  <section class="card card-front" aria-label="Business card, front">
    <span class="wordmark">TALVO SYSTEMS</span>
    <div class="contact">
      <p class="person"><span class="name">Lukas Brenner</span><span class="role">Web Developer</span></p>
      <p class="line company">Talvo Systems</p>
      <p class="line">+41 78 412 65 08</p>
      <p class="line">lukas@talvo-systems.ch</p>
      <p class="line">www.talvo-systems.ch</p>
    </div>
  </section>
</body>
</html>
```